Building company buisness cards

We are looking for a sharp modern new look for our business cards.
We are a New Zealand based company that specialises in house and land packages.
We have attached a photo of the current logo and would like to see if it can be improved somehow if needed.
We are open to any colours but we have chosen green at this stage.
Feel free to change the font and make the logo smarter looking.
Play with the colours and see what looks best.

We want a card that looks so good know one will want to throw it away!

Target Market(s)

Home buyers

Industry/Entity Type

Building

Contact Information for Business Card

Derek Tolvane
0217394062
dtolvane@quillmarkhomesteads.co.nz
quillmarkhomesteads.co.nz

Font styles to use
Serif
Sans Serif

Colors

Designer to choose colors to be used in the design.

Requirements
Must have
• Logo and company name on one side, details on the other side
Nice to have
• Color codes for the original green are HEX #4a8028, RGB(74,128,40), CMYK(42,0,69,50)
• Round corners, Raised and/or spot UV

```html
<!DOCTYPE html>
<html lang="en">
<head>
<meta charset="utf-8">
<title>Quillmark Homesteads – Business Cards</title>
<link href="https://fonts.googleapis.com/css2?family=Source+Sans+3:wght@400;600;800&family=Arimo:wght@700&display=swap" rel="stylesheet">
<style>
  :root {
    --green: #4a8028;
    --grey-bg: #c8c9cb;
    --arc-grey: #6d6d6f;
    --white: #ffffff;
    --ink: #2b2b2b;
  }
  html, body {
    margin: 0;
    padding: 0;
    width: 1200px;
    height: 1015px;
    overflow: hidden;
    background: var(--grey-bg);
  }
  .stage {
    position: relative;
    width: 1200px;
    height: 1015px;
  }
  .card {
    position: absolute;
    width: 687px;
    height: 392px;
    background: var(--white);
    border-radius: 34px;
    overflow: hidden;
    box-shadow: 0 3px 9px rgba(0,0,0,0.3);
    font-family: "Source Sans 3", sans-serif;
  }
  .card--front { left: 69px; top: 72px; }
  .card--back  { left: 414px; top: 525px; }

  .brand {
    position: absolute;
    left: 0; right: 0;
    display: flex;
    align-items: center;
    justify-content: center;
    gap: 12px;
    color: var(--green);
    font-weight: 800;
  }
  .brand__mark {
    width: 26px;
    height: 26px;
    background: var(--green);
  }
  .card--front .brand { top: 62px; font-size: 36px; letter-spacing: -0.5px; }

  .holder-name {
    position: absolute;
    top: 180px;
    left: 0; right: 0;
    text-align: center;
    padding-right: 38px;
    font-family: "Arimo", sans-serif;
    font-weight: 700;
    font-size: 26px;
    color: var(--green);
  }
  .band {
    position: absolute;
    left: 0; top: 0;
  }
  .contact {
    position: absolute;
    left: 0; right: 0;
    color: var(--white);
    display: flex;
    justify-content: center;
    align-items: center;
  }
  .contact--phone { top: 294px; font-size: 22px; gap: 7px; }
  .contact--web { top: 333px; font-size: 15.5px; gap: 12px; letter-spacing: -0.2px; }
  .contact__item { display: flex; align-items: center; gap: 7px; }
  .icon { display: block; }

  .card--back .brand {
    top: 118px;
    flex-direction: column;
    gap: 0;
    line-height: 1;
  }
  .brand__line1 { font-size: 34px; }
  .brand__line2 { font-size: 46px; letter-spacing: -0.5px; }
  .rule {
    position: absolute;
    top: 286px;
    left: 254px;
    width: 152px;
    height: 2px;
    background: var(--green);
  }
  .site {
    position: absolute;
    top: 344px;
    left: 0; right: 0;
    text-align: center;
    font-size: 17px;
    letter-spacing: 2.4px;
    color: var(--ink);
  }
  .site__name { color: var(--green); }
</style>
</head>
<body>
<main class="stage">

  <section class="card card--front" aria-label="Business card front">
    <div class="brand">
      <span class="brand__mark"></span>
      <span class="brand__name">Quillmark Homesteads</span>
    </div>

    <div class="holder-name">Derek Tolvane</div>

    <svg class="band" width="687" height="392" viewBox="0 0 687 392" aria-hidden="true">
      <path d="M0 316 Q343 160 687 312 Q343 178 0 316 Z" fill="var(--arc-grey)"/>
      <path d="M0 322 Q343 178 687 322 L687 392 L0 392 Z" fill="var(--green)"/>
    </svg>

    <div class="contact contact--phone">
      <svg class="icon" width="20" height="20" viewBox="0 0 20 20" aria-hidden="true">
        <circle cx="10" cy="10" r="8.5" fill="none" stroke="#fff" stroke-width="1.4"/>
        <path d="M7 5.5 L8.6 7.6 L7.8 8.6 Q9 11.4 11.4 12.4 L12.4 11.5 L14.4 13 L13.2 14.5 Q8 13.8 5.8 7 Z" fill="#fff"/>
      </svg>
      <span>0217394062</span>
    </div>

    <div class="contact contact--web">
      <span class="contact__item">
        <svg class="icon" width="16" height="13" viewBox="0 0 16 13" aria-hidden="true">
          <path d="M1 5 L8 1 L15 5 L15 12 L1 12 Z" fill="#fff"/>
          <path d="M1 5 L8 9 L15 5" fill="none" stroke="var(--green)" stroke-width="1.2"/>
        </svg>
        <span>dtolvane@quillmarkhomesteads.co.nz</span>
      </span>
      <span class="contact__item">
        <svg class="icon" width="15" height="15" viewBox="0 0 16 16" aria-hidden="true">
          <g fill="none" stroke="#fff" stroke-width="1.2">
            <circle cx="8" cy="8" r="6.8"/>
            <ellipse cx="8" cy="8" rx="3" ry="6.8"/>
            <line x1="1.2" y1="8" x2="14.8" y2="8"/>
            <line x1="2.5" y1="4.5" x2="13.5" y2="4.5"/>
            <line x1="2.5" y1="11.5" x2="13.5" y2="11.5"/>
          </g>
        </svg>
        <span>www.quillmarkhomesteads.co.nz</span>
      </span>
    </div>
  </section>

  <section class="card card--back" aria-label="Business card back">
    <div class="brand">
      <span class="brand__line1">Quillmark</span>
      <span class="brand__line2">Homesteads</span>
    </div>
    <div class="rule"></div>
    <div class="site">www.<span class="site__name">quillmarkhomesteads</span>.co.nz</div>
  </section>

</main>
</body>
</html>
```